GTP biz card

We need a business card design for our new company based in Los Angeles called "Gold Tide Pictures". We develop film and television projects. We work with investors, financiers, film production companies, film distribution and sales companies as well as studios. We would like to incorporate our logo (see attached) on a two-sided card. We need to include: name and title, address, phone, email and company website.

Target Market(s)

Business, financial and studio clients

Industry/Entity Type

Business

Contact Information for Business Card

Two-sided. We are thinking of the logo on one side and the information on the back. Please feel free to be creative! Thanks.

Requirements
Must have
• Please include the following text information, excluding the "CAPS CATEGORY:" and please allow the ability for us to change the name, title and email address for each company employee):
• NAME & TITLE:
• Neil Parker
• Managing Partner
• COMPANY NAME:
• GOLD TIDE PICTURES (please use existing logo)
• COMPANY ADDRESS:
• KTW Studio Park
• 2250 Halverd Street
• Harbor Wing, 4th Floor
• Manhattan Beach, CA 90412
• COMPANY PHONE NUMBER:
• 310-555-0148
• COMPANY WEBSITE ADDRESS:
• www.goldtidepicturesgroup.example
• EMAIL ADDRESS: (only one per card)
• peter@goldtidepicturesgroup.example
• bingo@goldtidepicturesgroup.example
• neil@goldtidepicturesgroup.example

```html
<!DOCTYPE html>
<html lang="en">
<head>
<meta charset="utf-8">
<title>Gold Tide Pictures – Business Card</title>
<link rel="stylesheet" href="https://fonts.googleapis.com/css2?family=Lato:wght@400;700;900&display=swap">
<style>
  :root {
    --bg: #2a2a2b;
    --card: #0b0b0c;
    --card-edge: #161618;
    --teal: #5fc6cf;
    --teal-deep: #0e5866;
    --teal-glow: #1b8a9c;
    --tab: #a9dcea;
    --tab-icon: #163944;
    --white: #f2f4f5;
    --grey: #b7babd;
    --muted: #8d9196;
  }
  * { margin: 0; padding: 0; box-sizing: border-box; }
  html, body {
    width: 1200px; height: 900px; overflow: hidden;
    background: var(--bg);
    font-family: "Lato", Arial, sans-serif;
  }
  .canvas { position: relative; width: 1200px; height: 900px; }

  .card {
    position: absolute;
    width: 560px; height: 320px;
    background: var(--card);
    border: 1px solid var(--card-edge);
    overflow: hidden;
    box-shadow: 0 14px 34px rgba(0,0,0,.55);
  }
  .card--front { left: 100px; top: 110px; }
  .card--back  { left: 540px; top: 470px; }

  /* Front */
  .brand {
    position: absolute; left: 0; right: 0; top: 88px;
    display: flex; flex-direction: column; align-items: center;
  }
  .brand__mark {
    width: 74px; height: 74px; border-radius: 50%;
    background: radial-gradient(circle at 50% 45%, var(--teal) 0%, var(--teal-glow) 45%, var(--teal-deep) 100%);
    box-shadow: 0 0 40px rgba(40,160,185,.45);
  }
  .brand__name {
    margin-top: 22px;
    font-weight: 900; font-size: 30px; letter-spacing: 4px;
    color: var(--teal);
  }
  .brand__tagline {
    margin-top: 8px;
    font-weight: 700; font-size: 11px; letter-spacing: 3px;
    color: var(--grey);
  }

  /* Back */
  .back__orb {
    position: absolute; right: -40px; top: -70px;
    width: 260px; height: 260px; border-radius: 50%;
    background: radial-gradient(circle at 45% 50%, #2a6f7a 0%, #113a44 45%, #08181d 75%, rgba(8,24,29,0) 100%);
  }
  .person { position: absolute; left: 62px; top: 46px; }
  .person__name {
    font-weight: 400; font-size: 21px; color: var(--teal); letter-spacing: .5px;
  }
  .person__title {
    margin-top: 2px; font-weight: 700; font-size: 14px; color: var(--white);
  }
  .person__address {
    margin-top: 10px; font-style: normal;
    font-size: 11px; line-height: 15px; color: var(--grey);
  }
  .contact__tab {
    position: absolute; left: 0; top: 186px;
    width: 40px; height: 100px;
    background: var(--tab);
    border-radius: 0 10px 10px 0;
    display: flex; flex-direction: column; align-items: center; justify-content: space-around;
    padding: 8px 0;
  }
  .contact__tab svg { width: 18px; height: 18px; }
  .contact__list {
    position: absolute; left: 56px; top: 190px;
    list-style: none;
    font-size: 14px; color: var(--white); line-height: 31px;
  }
  .back__tagline {
    position: absolute; right: 28px; bottom: 22px;
    font-weight: 700; font-size: 13px; letter-spacing: 3px; color: var(--grey);
  }
</style>
</head>
<body>
<main class="canvas">

  <section class="card card--front" aria-label="Business card front">
    <div class="brand">
      <div class="brand__mark"></div>
      <div class="brand__name">GOLD TIDE PICTURES</div>
      <div class="brand__tagline">A MEDIA ENTERTAINMENT COMPANY</div>
    </div>
  </section>

  <section class="card card--back" aria-label="Business card back">
    <div class="back__orb"></div>

    <div class="person">
      <div class="person__name">NEIL PARKER</div>
      <div class="person__title">Managing Partner</div>
      <address class="person__address">
        KTW Studio Park<br>
        2250 Halverd Street<br>
        Harbor Wing, 4th Floor<br>
        Manhattan Beach, CA 90412
      </address>
    </div>

    <div class="contact__tab">
      <svg viewBox="0 0 24 24" aria-label="Phone">
        <path fill="var(--tab-icon)" d="M6.6 10.8a15 15 0 0 0 6.6 6.6l2.2-2.2a1 1 0 0 1 1-.25 11.4 11.4 0 0 0 3.6.57 1 1 0 0 1 1 1V20a1 1 0 0 1-1 1A17 17 0 0 1 3 4a1 1 0 0 1 1-1h3.5a1 1 0 0 1 1 1c0 1.25.2 2.45.57 3.57a1 1 0 0 1-.25 1z"/>
      </svg>
      <svg viewBox="0 0 24 24" aria-label="Email">
        <rect x="2" y="5" width="20" height="14" rx="1.5" fill="var(--tab-icon)"/>
        <path d="M3 6l9 7 9-7" fill="none" stroke="var(--tab)" stroke-width="1.6"/>
      </svg>
      <svg viewBox="0 0 24 24" aria-label="Website">
        <g fill="none" stroke="var(--tab-icon)" stroke-width="2.4" stroke-linecap="round">
          <path d="M10 14a4 4 0 0 0 5.6 0l3.2-3.2a4 4 0 0 0-5.6-5.6L12 6.4"/>
          <path d="M14 10a4 4 0 0 0-5.6 0l-3.2 3.2a4 4 0 0 0 5.6 5.6L12 17.6"/>
        </g>
      </svg>
    </div>

    <ul class="contact__list">
      <li>310-555-0148</li>
      <li>neil@goldtidepicturesgroup.example</li>
      <li>www.goldtidepicturesgroup.example</li>
    </ul>

    <div class="back__tagline">FILM AND TELEVISION</div>
  </section>

</main>
</body>
</html>
```